Create a memorable Stationary for Security Software Company

Velbrantix is the worldwide leader in securing the Internet. Making Internet communications and critical data secure, reliable and available everywhere has been and continues to be our ongoing vision. We are committed to staying focused on real customer needs and to developing new and innovative security solutions that redefine the security landscape.

Industry/Entity Type

Internet

Font styles to use
Serif
Sans Serif
Script

Colors
0792cd
33a6d7
85cae6

```html
<!DOCTYPE html>
<html lang="en">
<head>
<meta charset="utf-8">
<title>Velbrantix Business Cards</title>
<link href="https://fonts.googleapis.com/css2?family=Source+Sans+3:wght@400;600;700&display=swap" rel="stylesheet">
<style>
  :root {
    --brand-deep: #0792cd;
    --brand-blue: #33a6d7;
    --brand-light: #85cae6;
    --paper: #ffffff;
    --ink: #2b2b2b;
    --night: #000000;
    --backdrop: #ecebe8;
    --rule: #9a9a9a;
  }
  * { margin: 0; padding: 0; box-sizing: border-box; }
  html, body { width: 1200px; height: 750px; overflow: hidden; }
  body {
    background: var(--backdrop);
    font-family: "Source Sans 3", "Myriad Pro", Arial, sans-serif;
    position: relative;
  }
  .card {
    position: absolute;
    width: 530px;
    height: 302px;
    border-radius: 22px;
    overflow: hidden;
    box-shadow: 0 2px 6px rgba(0,0,0,0.18);
  }
  .card--light { left: 51px; top: 52px; background: var(--paper); color: var(--ink); }
  .card--dark { left: 622px; top: 52px; background: var(--night); color: var(--paper); }
  .card--back { left: 333px; top: 400px; background: var(--night); }

  .card__wave { position: absolute; inset: 0; width: 100%; height: 100%; }

  .brand {
    position: absolute;
    display: flex;
    align-items: center;
    gap: 10px;
  }
  .card--light .brand, .card--dark .brand { left: 40px; top: 86px; }
  .brand__dot {
    width: 26px; height: 26px; border-radius: 50%;
    background: var(--brand-blue);
  }
  .brand__name {
    font-weight: 700;
    font-size: 40px;
    color: var(--brand-blue);
    letter-spacing: 0.5px;
  }

  .divider {
    position: absolute;
    left: 290px; top: 40px;
    width: 1px; height: 146px;
    background: var(--rule);
  }
  .contact {
    position: absolute;
    left: 312px; top: 44px;
    list-style: none;
    font-size: 14px;
    line-height: 22.5px;
  }
  .contact li { display: flex; align-items: center; gap: 7px; }
  .contact svg { width: 11px; height: 11px; fill: var(--brand-blue); flex: none; }
  .address {
    position: absolute;
    left: 312px; top: 145px;
    font-size: 14px;
    line-height: 18px;
  }

  .person {
    position: absolute;
    left: 340px; top: 234px;
    width: 200px;
    text-align: center;
    color: var(--paper);
  }
  .person__name { font-weight: 700; font-size: 21px; line-height: 26px; }
  .person__title { font-weight: 400; font-size: 19px; line-height: 24px; }

  .card--back .brand {
    left: 0; right: 0; top: 108px;
    justify-content: center;
  }
  .card--back .brand__name { font-size: 46px; }
  .back__web {
    position: absolute;
    left: 0; right: 0; top: 228px;
    text-align: center;
    color: var(--paper);
    font-size: 16px;
    letter-spacing: 3.2px;
  }
</style>
</head>
<body>

  <section class="card card--light">
    <svg class="card__wave" viewBox="0 0 530 302" aria-hidden="true">
      <path d="M0,190 C30,285 260,275 530,182 V302 H0 Z" fill="var(--brand-blue)"/>
      <path d="M32,282 C210,286 380,220 530,186 L530,196 C390,232 220,292 32,282 Z" fill="var(--paper)"/>
    </svg>
    <div class="brand"><span class="brand__dot"></span><span class="brand__name">Velbrantix</span></div>
    <div class="divider"></div>
    <ul class="contact">
      <li><svg viewBox="0 0 10 10"><path d="M2,0.5 L4,2.5 L3,3.8 C3.8,5.3 4.7,6.2 6.2,7 L7.5,6 L9.5,8 L8,9.5 C4,9 1,6 0.5,2 Z"/></svg>012-345-6789</li>
      <li><svg viewBox="0 0 10 10"><path d="M2.5,0 H7.5 V10 H2.5 Z M3.5,1.2 V7.5 H6.5 V1.2 Z"/></svg>012-345-6789</li>
      <li><svg viewBox="0 0 10 10"><path d="M0,2 H10 V9 H0 Z M0.8,2.6 L5,6 L9.2,2.6 Z" fill-rule="evenodd"/></svg>info@velbrantix.com</li>
      <li><svg viewBox="0 0 10 10"><circle cx="5" cy="5" r="4.6"/><path d="M0.5,5 H9.5 M5,0.5 V9.5" stroke="var(--paper)" stroke-width="0.8"/></svg>www.velbrantix.com</li>
    </ul>
    <p class="address">Street Name, City Name<br>Zipcode-012345</p>
    <div class="person">
      <p class="person__name">Your Name</p>
      <p class="person__title">Title</p>
    </div>
  </section>

  <section class="card card--dark">
    <svg class="card__wave" viewBox="0 0 530 302" aria-hidden="true">
      <path d="M0,190 C30,285 260,275 530,182 V302 H0 Z" fill="var(--brand-blue)"/>
      <path d="M32,282 C210,286 380,220 530,186 L530,196 C390,232 220,292 32,282 Z" fill="var(--night)"/>
    </svg>
    <div class="brand"><span class="brand__dot"></span><span class="brand__name">Velbrantix</span></div>
    <div class="divider"></div>
    <ul class="contact">
      <li><svg viewBox="0 0 10 10"><path d="M2,0.5 L4,2.5 L3,3.8 C3.8,5.3 4.7,6.2 6.2,7 L7.5,6 L9.5,8 L8,9.5 C4,9 1,6 0.5,2 Z"/></svg>012-345-6789</li>
      <li><svg viewBox="0 0 10 10"><path d="M2.5,0 H7.5 V10 H2.5 Z M3.5,1.2 V7.5 H6.5 V1.2 Z"/></svg>012-345-6789</li>
      <li><svg viewBox="0 0 10 10"><path d="M0,2 H10 V9 H0 Z M0.8,2.6 L5,6 L9.2,2.6 Z" fill-rule="evenodd"/></svg>info@velbrantix.com</li>
      <li><svg viewBox="0 0 10 10"><circle cx="5" cy="5" r="4.6"/><path d="M0.5,5 H9.5 M5,0.5 V9.5" stroke="var(--night)" stroke-width="0.8"/></svg>www.velbrantix.com</li>
    </ul>
    <p class="address">Street Name, City Name<br>Zipcode-012345</p>
    <div class="person">
      <p class="person__name">Your Name</p>
      <p class="person__title">Title</p>
    </div>
  </section>

  <section class="card card--back">
    <div class="brand"><span class="brand__dot"></span><span class="brand__name">Velbrantix</span></div>
    <p class="back__web">www.velbrantix.com</p>
  </section>

</body>
</html>
```